BOLD & MINIMALIST DESIGN NEEDED

We want a very bold but minimalistic business card design that is impactful and utilizes both sides of the business card. Our current logo is included for your use.

We want bold fonts and good use of negative space. We don't want the logo to overpower the design.

Target Market(s)

Professionals who are building new commercial buildings.

Industry/Entity Type

Construction

Contact Information for Business Card

Name, Title, email, office phone, cell phone, website

Font styles to use
Serif
Sans Serif

Requirements
Must have
• Bold design!

```html
<!DOCTYPE html>
<html lang="en">
<head>
<meta charset="utf-8">
<title>Stonecrest Business Card</title>
<link href="https://fonts.googleapis.com/css2?family=Roboto:wght@400;700;900&display=swap" rel="stylesheet">
<style>
  :root {
    --green: #7fbf27;
    --green-light: #a9d46e;
    --black: #050505;
    --white: #f3f3f3;
    --page: #e4e4e4;
  }
  html, body {
    margin: 0;
    padding: 0;
    width: 1200px;
    height: 1040px;
    overflow: hidden;
    background: var(--page);
    font-family: "Roboto", Arial, sans-serif;
  }
  .card {
    position: absolute;
    left: 280px;
    width: 644px;
    height: 366px;
    border-radius: 16px;
    overflow: hidden;
    box-shadow: 0 3px 6px rgba(0,0,0,0.25);
  }
  .card-front { top: 130px; background: var(--white); }
  .card-back {
    top: 568px;
    background: radial-gradient(ellipse at 50% 45%, var(--green-light) 0%, var(--green) 75%);
  }
  .wave { position: absolute; inset: 0; width: 100%; height: 100%; }
  .brand {
    position: absolute;
    display: flex;
    align-items: center;
    gap: 10px;
    font-weight: 900;
    color: var(--black);
    letter-spacing: 1px;
  }
  .brand-mark { background: var(--black); display: block; }
  .card-front .brand { left: 44px; top: 125px; font-size: 36px; }
  .card-front .brand-mark { width: 26px; height: 26px; }
  .card-back .brand {
    left: 0; right: 0; top: 150px;
    justify-content: center;
    font-size: 64px;
  }
  .card-back .brand-mark { width: 44px; height: 44px; }
  .contact {
    position: absolute;
    right: 40px;
    top: 160px;
    text-align: right;
    color: #fff;
  }
  .contact-name {
    margin: 0;
    color: var(--green);
    font-weight: 700;
    font-size: 25px;
    line-height: 30px;
  }
  .contact-title { margin: 0 0 12px; font-size: 17px; line-height: 20px; }
  .contact-address { margin: 0 0 12px; font-size: 16px; line-height: 20px; font-style: normal; }
  .contact-lines { list-style: none; margin: 0; padding: 0; font-size: 16px; line-height: 20px; }
  .contact-lines li { display: flex; justify-content: flex-end; align-items: center; gap: 12px; }
  .contact-lines svg { width: 13px; height: 13px; fill: var(--green); }
</style>
</head>
<body>

<section class="card card-front">
  <svg class="wave" viewBox="0 0 800 456" preserveAspectRatio="none" aria-hidden="true">
    <path fill="var(--green)" d="M0,285 C110,350 210,380 290,365 C380,345 450,270 530,195 C620,110 700,62 800,72 L800,85 C700,70 620,110 520,190 C430,260 350,350 260,380 C200,400 120,400 0,330 Z"/>
    <path fill="var(--black)" stroke="#fff" stroke-width="3" d="M0,330 C120,400 200,400 260,380 C350,350 430,260 520,190 C620,110 700,70 800,85 L800,460 L0,460 Z"/>
  </svg>

  <div class="brand"><span class="brand-mark"></span>STONECREST</div>

  <div class="contact">
    <h1 class="contact-name">DANIEL HARPER</h1>
    <p class="contact-title">President</p>
    <address class="contact-address">4127 Kingsbury Lane<br>Oak Ridge, NY 11020</address>
    <ul class="contact-lines">
      <li>(555) 8210-4476
        <svg viewBox="0 0 24 24"><path d="M6.6 10.8a15.1 15.1 0 0 0 6.6 6.6l2.2-2.2a1 1 0 0 1 1-.25 11.4 11.4 0 0 0 3.6.57 1 1 0 0 1 1 1V20a1 1 0 0 1-1 1A17 17 0 0 1 3 4a1 1 0 0 1 1-1h3.5a1 1 0 0 1 1 1c0 1.25.2 2.45.57 3.57a1 1 0 0 1-.25 1z"/></svg>
      </li>
      <li>info@stonecrestbuild.com
        <svg viewBox="0 0 24 24"><path d="M2 5h20v14H2z M2 5l10 8 10-8" stroke="#000" stroke-width="1.5"/></svg>
      </li>
      <li>www.stonecrestbuild.com
        <svg viewBox="0 0 24 24"><circle cx="12" cy="12" r="10"/><path d="M2 12h20M12 2c3 3 3 17 0 20M12 2c-3 3-3 17 0 20" stroke="#000" stroke-width="1.5" fill="none"/></svg>
      </li>
    </ul>
  </div>
</section>

<section class="card card-back">
  <div class="brand"><span class="brand-mark"></span>STONECREST</div>
</section>

</body>
</html>
```